SkyvornQ Business Cards and Stationary Design

Need a design for our business cards and stationary. I want to carry on the theme of the logo. I want the business cards to have a design on the back. I would like the business cards and the stationary to carry the same theme, design scheme, and branding

Target Market(s)

Airlines and Maintenance Facilities

Industry/Entity Type

Aviation

Contact Information for Business Card

Name
Position Title
Address: 4827 Trellis Hollow Road, Fort Pierce, Florida, 34951
Office Number
Mobile Number
Email
Website

Font styles to use
Serif
Sans Serif

Colors

Designer to choose colors to be used in the design.

```html
<!DOCTYPE html>
<html lang="en">
<head>
<meta charset="utf-8">
<title>SkyvornQ Business Card</title>
<link href="https://fonts.googleapis.com/css2?family=Roboto:wght@400;500;700&display=swap" rel="stylesheet">
<style>
  :root {
    --backdrop: #2f2f31;
    --navy: #072448;
    --blue-deep: #0b3a86;
    --blue-bright: #0aa3e6;
    --blue-title: #1e9fe6;
    --white: #ffffff;
  }
  * { margin: 0; padding: 0; box-sizing: border-box; }
  html, body {
    width: 1200px; height: 960px; overflow: hidden;
    background: var(--backdrop);
    font-family: "Roboto", Arial, sans-serif;
  }
  .card {
    position: absolute;
    width: 600px; height: 342px;
    border-radius: 20px;
    overflow: hidden;
  }
  .card-front { left: 313px; top: 113px; }
  .card-back { left: 311px; top: 473px; background: var(--navy); }
  .front-art { position: absolute; inset: 0; }
  .contact-block { position: absolute; left: 32px; top: 68px; color: var(--white); }
  .person-name { font-size: 21px; font-weight: 700; letter-spacing: 0.3px; line-height: 1; }
  .person-role { font-size: 14px; font-weight: 500; color: var(--blue-title); margin-top: 6px; }
  .address { font-size: 14px; line-height: 18px; margin-top: 24px; }
  .contact-list { list-style: none; margin-top: 11px; font-size: 14px; }
  .contact-list li { display: flex; align-items: center; height: 19px; }
  .contact-list svg { width: 13px; height: 13px; margin-right: 10px; flex: none; }
  .brand-front {
    position: absolute; left: 250px; right: 0; top: 112px;
    display: flex; flex-direction: column; align-items: center;
  }
  .brand-dot {
    width: 40px; height: 40px; border-radius: 50%;
    background: var(--blue-bright);
  }
  .brand-front .brand-name {
    margin-top: 26px; font-size: 30px; font-weight: 700;
    letter-spacing: 4px; color: var(--navy);
  }
  .brand-back {
    position: absolute; left: 0; right: 0; top: 110px;
    display: flex; flex-direction: column; align-items: center;
  }
  .brand-back .brand-dot { background: var(--white); width: 46px; height: 46px; }
  .brand-back .brand-name {
    margin-top: 22px; font-size: 44px; font-weight: 700;
    letter-spacing: 5px; color: var(--white);
  }
  .back-web {
    position: absolute; left: 0; right: 0; top: 289px;
    text-align: center; color: var(--white);
    font-size: 14px; letter-spacing: 5px;
  }
</style>
</head>
<body>
  <section class="card card-front">
    <svg class="front-art" viewBox="0 0 600 342" width="600" height="342">
      <defs>
        <radialGradient id="frontGlow" cx="0.42" cy="0.5" r="0.55">
          <stop offset="0" stop-color="#0ab0f0"/>
          <stop offset="0.55" stop-color="#0870c4"/>
          <stop offset="1" stop-color="#0b3a86"/>
        </radialGradient>
      </defs>
      <rect width="600" height="342" fill="url(#frontGlow)"/>
      <path d="M395,0 C290,0 232,80 232,172 C232,265 290,342 385,342 L600,342 L600,0 Z" fill="var(--white)"/>
      <path d="M400,0 C295,0 238,80 238,172 C238,265 295,342 390,342 L600,342 L600,0 Z" fill="var(--navy)"/>
      <path d="M408,0 C303,0 246,80 246,172 C246,265 303,342 398,342 L600,342 L600,0 Z" fill="var(--white)"/>
    </svg>
    <div class="contact-block">
      <div class="person-name">DANIEL REYES</div>
      <div class="person-role">CEO/FOUNDER</div>
      <div class="address">4827 Trellis Hollow Road<br>Fort Pierce, Florida, 34951</div>
      <ul class="contact-list">
        <li><svg viewBox="0 0 16 16"><path d="M3 1l3 1 1 3-2 1.5c1 2 2.5 3.5 4.5 4.5L11 9l3 1 1 3-2 2C7 15 1 9 1 3z" fill="var(--blue-title)"/></svg>772 418 3065</li>
        <li><svg viewBox="0 0 16 16"><rect x="4" y="0.5" width="8" height="15" rx="1.5" fill="none" stroke="var(--blue-title)" stroke-width="1.6"/><circle cx="8" cy="12.8" r="1" fill="var(--blue-title)"/></svg>772 590 1847</li>
        <li><svg viewBox="0 0 16 16"><rect x="1" y="3" width="14" height="10" fill="var(--blue-title)"/><path d="M1 3l7 6 7-6" fill="none" stroke="#0b5aa8" stroke-width="1.2"/></svg>info@skyvornq.com</li>
        <li><svg viewBox="0 0 16 16"><circle cx="8" cy="8" r="7" fill="var(--blue-title)"/><path d="M1 8h14M8 1c-3 3-3 11 0 14M8 1c3 3 3 11 0 14" fill="none" stroke="#0b5aa8" stroke-width="1"/></svg>www.skyvornq.com</li>
      </ul>
    </div>
    <div class="brand-front">
      <div class="brand-dot"></div>
      <div class="brand-name">SKYVORNQ</div>
    </div>
  </section>

  <section class="card card-back">
    <div class="brand-back">
      <div class="brand-dot"></div>
      <div class="brand-name">SKYVORNQ</div>
    </div>
    <div class="back-web">www.skyvornq.com</div>
  </section>
</body>
</html>
```